ourTradeLoop Webdesign - trading your electronics for cash - helping you clear up clutter

We need web design (and an updated logo) for a new company based in London called "ourTradeLoop". It is a platform that enables users to sell their old electronics for cash, either for themselves or they can donate the cash to charity. In time, we also plan to enable buying of electronics on the site. We specialise in mobile phones, tablets, laptops, and games consoles. Please review brindlo.com, which is a US site with the same business, and also tunefernwick.co.uk, so have a similar business in the UK. We would like to see designs that use the colour red, and that are bold. We currently have a logo, and a WIP site built, but the design needs to be dramatically improved, the right colour mix needs to be chosen to give a clean and modern feel. Please review www.ourtradeloop.com to get an understanding of the work that needs to be improved.

Target Market(s)

People who buy electronics frequently, i.e. upgrade every time a new quince product comes out! These guys usually have a lap top, desk top, tablet and phone.

Industry/Entity Type

Electronics

Logo Text

ourTradeLoop

Number of Pages Required

3 page

Font styles to use
Sans Serif

Colors
ec1f27

Requirements
Must have
• Home page design
• "How-it-works" page design
• Sell page design
• Must use the colour red, and have a secondary/accent colour.

```html
<!DOCTYPE html>
<html lang="en">
<head>
<meta charset="utf-8">
<title>ourTradeLoop – Sell Your Electronics</title>
<link rel="stylesheet" href="https://fonts.googleapis.com/css2?family=Montserrat:wght@400;600;700;800&family=Open+Sans:wght@400;600;700&display=swap">
<style>
:root{
  --red:#ec1f27;
  --red-dark:#c8161d;
  --ink:#222222;
  --text:#6f6f6f;
  --muted:#9a9a9a;
  --light:#f2f2f2;
  --line:#e2e2e2;
  --navy:#2b2f45;
  --navy-deep:#22253a;
  --green:#8cc63f;
  --yellow:#f4c51c;
  --blue:#3fa9e0;
  --coral:#f0605d;
  --orange:#f7931e;
  --white:#ffffff;
}
*{box-sizing:border-box;margin:0;padding:0}
html,body{width:1200px;height:2356px;overflow:hidden}
body{font-family:"Open Sans",Arial,sans-serif;color:var(--text);background:var(--white);font-size:13px;line-height:1.6}
a{color:inherit;text-decoration:none}

/* header */
.site-header{height:56px;display:flex;align-items:center;justify-content:space-between;padding:0 60px}
.brand{display:flex;align-items:center;gap:8px;font-family:"Montserrat",sans-serif;font-weight:700;font-size:22px;color:var(--ink)}
.brand-dot{width:18px;height:18px;border-radius:50%;background:var(--red)}
.main-nav{display:flex;align-items:center;gap:26px;font-family:"Montserrat",sans-serif;font-size:13px;color:var(--ink);font-weight:600}
.nav-btn{border:2px solid var(--ink);padding:5px 16px}
.nav-btn.red{border-color:var(--red);color:var(--red)}

/* hero */
.hero{position:relative;height:454px;background:linear-gradient(90deg,#dcdcdc,#f4f4f4 60%,#e6e6e6);overflow:hidden}
.hero-red{position:absolute;inset:0}
.hero-photo{position:absolute;border-radius:26px}
.phone-dark{left:150px;top:30px;width:190px;height:380px;background:linear-gradient(160deg,#3a3f48,#14161a);transform:rotate(-6deg)}
.phone-light{left:610px;top:10px;width:380px;height:440px;background:linear-gradient(160deg,#ffffff,#cfd3d8);border-radius:40px;transform:rotate(8deg)}
.tag{position:absolute;color:var(--white);font-family:"Montserrat",sans-serif;padding:10px 26px}
.tag strong{display:block;font-size:64px;line-height:1;font-weight:800;letter-spacing:1px}
.tag span{font-size:18px;font-weight:600}
.tag-sell{left:620px;top:225px;background:var(--ink);width:260px}
.tag-buy{left:130px;top:330px;background:var(--red);width:300px}

/* sections */
.section-title{font-family:"Montserrat",sans-serif;font-weight:700;font-size:26px;color:var(--ink);text-align:center;text-transform:uppercase}
.section-lead{max-width:760px;margin:14px auto 0;text-align:center;font-size:12px;color:var(--muted)}

.gadgets{height:418px;padding-top:122px}
.gadget-row{display:flex;justify-content:center;align-items:center;gap:52px;margin-top:52px}
.gadget{width:112px;height:112px;border-radius:50%;display:flex;align-items:center;justify-content:center;box-shadow:0 4px 0 rgba(0,0,0,.08)}
.gadget.green{background:var(--green)}
.gadget.yellow{background:var(--yellow)}
.gadget.blue{background:var(--blue)}
.gadget.coral{background:var(--coral)}
.gadget.orange{background:var(--orange)}
.slider-arrow{width:44px;height:44px;border-radius:50%;background:#d9d9d9;display:flex;align-items:center;justify-content:center}

.app{height:400px;background:var(--light);display:flex;padding:0 150px 0 150px}
.app-copy{width:560px;padding-top:78px}
.app-copy h2{font-family:"Montserrat",sans-serif;font-weight:700;font-size:26px;color:var(--ink);text-transform:uppercase}
.app-copy p{margin-top:14px;font-size:12px;color:var(--muted)}
.store-row{display:flex;gap:14px;margin-top:26px}
.store-badge{width:130px;height:42px;border-radius:7px;background:#111}
.app-photo{margin-left:auto;margin-top:30px;width:300px;height:370px;background:linear-gradient(170deg,#ffffff,#e3c4b3 60%,#c99a82);border-radius:6px}

.how{height:250px;padding-top:40px;text-align:center}
.btn-red{display:inline-block;margin-top:26px;background:var(--red);color:var(--white);font-family:"Montserrat",sans-serif;font-weight:700;font-size:12px;padding:12px 28px;text-transform:uppercase}

.why{height:400px;border-top:1px solid var(--line);margin:0 60px;padding-top:72px}
.why-row{display:flex;justify-content:center;gap:70px;margin-top:60px}
.feature{width:250px;text-align:center}
.feature svg{display:block;margin:0 auto 14px}
.feature h3{font-family:"Montserrat",sans-serif;font-weight:700;font-size:15px;color:var(--ink);text-transform:uppercase}
.feature p{margin-top:12px;font-size:12px;color:var(--muted)}

.newsletter{height:80px;background:var(--red);display:flex;align-items:center;padding:0 60px;color:var(--white)}
.newsletter-title{display:flex;align-items:center;gap:12px;font-family:"Montserrat",sans-serif;line-height:1.1}
.newsletter-title small{display:block;font-size:12px;font-weight:600}
.newsletter-title b{font-size:22px;font-weight:700}
.newsletter-form{display:flex;margin-left:120px}
.newsletter-form .field{width:540px;height:38px;background:var(--white);color:var(--muted);font-size:12px;padding:10px 14px}
.newsletter-form .submit{height:38px;border:2px solid var(--white);padding:0 24px;margin-left:10px;display:flex;align-items:center;font-family:"Montserrat",sans-serif;font-weight:700;font-size:12px}

.site-footer{height:250px;background:var(--navy);padding:46px 60px 0;display:flex;color:#b7bbce;font-size:12px}
.footer-about{width:290px}
.footer-about .brand{color:var(--white)}
.footer-about p{margin-top:12px;width:230px}
.cards{display:flex;gap:6px;margin-top:16px}
.cards span{width:36px;height:22px;border-radius:3px;background:#e9e9e9}
.footer-col{width:175px}
.footer-col h4{font-family:"Montserrat",sans-serif;font-weight:700;font-size:13px;color:var(--white);text-transform:uppercase;margin-bottom:10px}
.footer-col li{list-style:none;line-height:1.75}
.contact li{display:flex;gap:8px;align-items:flex-start}
.contact svg{flex:none;margin-top:4px}

.bottom-bar{height:48px;background:var(--navy-deep);display:flex;align-items:center;justify-content:space-between;padding:0 60px;color:#9a9fb6;font-size:11px}
.social{display:flex;align-items:center;gap:8px}
.social span{width:20px;height:20px;background:#c7cad8;border-radius:3px}
</style>
</head>
<body>

<header class="site-header">
  <a class="brand" href="#"><span class="brand-dot"></span>ourTradeLoop</a>
  <nav class="main-nav">
    <a href="#">How it works</a>
    <a href="#">Help</a>
    <a class="nav-btn red" href="#">Buy</a>
    <a class="nav-btn" href="#">Sell</a>
  </nav>
</header>

<section class="hero">
  <svg class="hero-red" width="1200" height="454" viewBox="0 0 1200 454" aria-hidden="true">
    <polygon points="0,0 700,0 560,454 0,454" fill="#ec1f27"/>
    <polygon points="560,454 700,0 760,0 600,454" fill="#c8161d"/>
  </svg>
  <div class="hero-photo phone-dark" role="img" aria-label="Dark smartphone photograph"></div>
  <div class="hero-photo phone-light" role="img" aria-label="White smartphone photograph"></div>
  <div class="tag tag-sell"><strong>SELL</strong><span>Cash Your Electronics</span></div>
  <div class="tag tag-buy"><strong>BUY</strong><span>Certified Electronics</span></div>
</section>

<section class="gadgets">
  <h2 class="section-title">Click your gadget to sell</h2>
  <p class="section-lead">Pick the device you want to sell, answer a few quick questions about its condition and get an instant cash offer. Free postage, fast payment and no hidden fees on every trade.</p>
  <div class="gadget-row">
    <span class="slider-arrow"><svg width="14" height="14" viewBox="0 0 14 14"><path d="M9 2 4 7l5 5" fill="none" stroke="#fff" stroke-width="2.5"/></svg></span>
    <a class="gadget green" href="#" aria-label="Desktops"><svg width="52" height="46" viewBox="0 0 52 46"><rect x="2" y="2" width="48" height="32" rx="3" fill="none" stroke="#fff" stroke-width="4"/><path d="M18 44h16M26 34v10" stroke="#fff" stroke-width="4"/></svg></a>
    <a class="gadget yellow" href="#" aria-label="Laptops"><svg width="56" height="40" viewBox="0 0 56 40"><rect x="8" y="2" width="40" height="28" rx="2" fill="none" stroke="#fff" stroke-width="4"/><path d="M2 36h52" stroke="#fff" stroke-width="5"/></svg></a>
    <a class="gadget blue" href="#" aria-label="Tablets"><svg width="38" height="52" viewBox="0 0 38 52"><rect x="2" y="2" width="34" height="48" rx="4" fill="none" stroke="#fff" stroke-width="4"/><circle cx="19" cy="43" r="2.5" fill="#fff"/></svg></a>
    <a class="gadget coral" href="#" aria-label="Phones"><svg width="28" height="52" viewBox="0 0 28 52"><rect x="2" y="2" width="24" height="48" rx="4" fill="none" stroke="#fff" stroke-width="4"/><circle cx="14" cy="43" r="2.5" fill="#fff"/></svg></a>
    <a class="gadget orange" href="#" aria-label="Games consoles"><svg width="58" height="36" viewBox="0 0 58 36"><path d="M14 4h30c8 0 12 8 12 20 0 10-8 12-12 4l-4-6H18l-4 6c-4 8-12 6-12-4C2 12 6 4 14 4z" fill="#fff"/><path d="M16 12v10M11 17h10" stroke="#f7931e" stroke-width="3"/><circle cx="40" cy="14" r="2.5" fill="#f7931e"/><circle cx="46" cy="20" r="2.5" fill="#f7931e"/></svg></a>
    <span class="slider-arrow"><svg width="14" height="14" viewBox="0 0 14 14"><path d="M5 2l5 5-5 5" fill="none" stroke="#fff" stroke-width="2.5"/></svg></span>
  </div>
</section>

<section class="app">
  <div class="app-copy">
    <h2>ourTradeLoop Mobile App</h2>
    <p>Trade on the move with our free app. Snap a photo of your gadget, get a price in seconds and book a free courier pickup from wherever you are. Track every order, see payment updates in real time and choose to give your cash to a charity you love. Clearing the clutter has never been this quick or this easy.</p>
    <div class="store-row">
      <span class="store-badge" role="img" aria-label="App store download badge"></span>
      <span class="store-badge" role="img" aria-label="App store download badge"></span>
    </div>
  </div>
  <div class="app-photo" role="img" aria-label="Hand holding a phone showing the ourTradeLoop app"></div>
</section>

<section class="how">
  <h2 class="section-title">How to sell your product</h2>
  <p class="section-lead">Choose your device, tell us its condition and accept our offer. Send it free with our prepaid label and we pay you the same day your item arrives and passes our checks.</p>
  <a class="btn-red" href="#">Click here to read more</a>
</section>

<section class="why">
  <h2 class="section-title">Why customers choose us</h2>
  <div class="why-row">
    <div class="feature">
      <svg width="60" height="40" viewBox="0 0 60 40"><rect x="2" y="6" width="34" height="22" fill="#ec1f27"/><path d="M36 12h12l8 9v7H36z" fill="#ec1f27"/><circle cx="14" cy="32" r="5" fill="#ec1f27" stroke="#fff" stroke-width="2"/><circle cx="46" cy="32" r="5" fill="#ec1f27" stroke="#fff" stroke-width="2"/></svg>
      <h3>Fast delivery</h3>
      <p>Free tracked postage on every trade, with prepaid labels sent straight to your inbox so your parcel is on its way today.</p>
    </div>
    <div class="feature">
      <svg width="40" height="40" viewBox="0 0 40 40"><path d="M20 2 36 8v12c0 10-8 16-16 18C12 36 4 30 4 20V8z" fill="#ec1f27"/><path d="M12 20l6 6 10-12" fill="none" stroke="#fff" stroke-width="3.5"/></svg>
      <h3>Safe &amp; secure payment</h3>
      <p>Paid by bank transfer or cheque within hours of checking your device, with full data wiping on every item we receive.</p>
    </div>
    <div class="feature">
      <svg width="40" height="40" viewBox="0 0 40 40"><circle cx="20" cy="20" r="18" fill="#ec1f27"/><path d="M13 20l5 5 9-11" fill="none" stroke="#fff" stroke-width="3.5"/></svg>
      <h3>100% money back guaranteed</h3>
      <p>Not happy with a revised offer? We send your gadget back to you free of charge, no questions asked and no cost.</p>
    </div>
  </div>
</section>

<section class="newsletter">
  <div class="newsletter-title">
    <svg width="34" height="26" viewBox="0 0 34 26"><rect x="1" y="1" width="32" height="24" fill="none" stroke="#fff" stroke-width="2"/><path d="M1 1l16 13L33 1" fill="none" stroke="#fff" stroke-width="2"/></svg>
    <div><small>NEWSLETTER</small><b>SUBSCRIPTION</b></div>
  </div>
  <div class="newsletter-form">
    <span class="field">Enter your email address</span>
    <span class="submit">SUBSCRIBE</span>
  </div>
</section>

<footer class="site-footer">
  <div class="footer-about">
    <a class="brand" href="#"><span class="brand-dot"></span>ourTradeLoop</a>
    <p>Sell your old phones, tablets, laptops and consoles for cash in minutes.</p>
    <div class="cards" role="img" aria-label="Accepted payment cards"><span></span><span></span><span></span></div>
  </div>
  <div class="footer-col">
    <h4>Quick links</h4>
    <ul><li>Contact</li><li>FAQ</li><li>Delivery</li><li>Returns</li><li>Track Orders</li><li>Subscribe</li></ul>
  </div>
  <div class="footer-col">
    <h4>Extras</h4>
    <ul><li>Specials</li><li>Manufacturers</li><li>Top sellers</li><li>Our stores</li><li>Contact us</li><li>Terms</li></ul>
  </div>
  <div class="footer-col">
    <h4>My account</h4>
    <ul><li>Delivery Information</li><li>Privacy Policy</li><li>Returns Policy</li><li>Terms and Conditions</li><li>Help</li></ul>
  </div>
  <div class="footer-col contact">
    <h4>Contact us</h4>
    <ul>
      <li><svg width="10" height="14" viewBox="0 0 10 14"><path d="M5 0a5 5 0 0 1 5 5c0 4-5 9-5 9S0 9 0 5a5 5 0 0 1 5-5z" fill="#ec1f27"/></svg><span>1045 Tarvin Avenue,<br>San Feldon, CA 94110</span></li>
      <li><svg width="12" height="12" viewBox="0 0 12 12"><path d="M2 0h3l1 3-2 1.5a7 7 0 0 0 3.5 3.5L9 6l3 1v3c0 1-1 2-2 2A10 10 0 0 1 0 2c0-1 1-2 2-2z" fill="#ec1f27"/></svg><span>1 555 018 2046</span></li>
      <li><svg width="12" height="10" viewBox="0 0 12 10"><rect width="12" height="10" fill="#ec1f27"/><path d="M0 0l6 5 6-5" fill="none" stroke="#fff"/></svg><span>info@ourtradeloop.com</span></li>
    </ul>
  </div>
</footer>

<div class="bottom-bar">
  <span>Copyright © 2016, ourTradeLoop. All Rights Reserved.</span>
  <div class="social">Follow us on <span></span><span></span><span></span><span></span><span></span><span></span></div>
</div>

</body>
</html>
```